Velan Tea Label & packaging for a premium tea brand. For local and global market

Create a look and feel for a box and rectangle tin. We are looking for a luxe packaging design for a new tea brand based in Kenya called 'Velan Tea'. Kenya is home to the finest teas in the world and Velan tea looks to embody that fact. Velan Tea uses the most premium of Kenyan Tea, Black tea, Purple tea, White Tea, Green tea, Hibiscus Tea and Moringa Tea. Velan Tea is handpicked from Kenya's highlands. This project will include the look and feel of the different teas described above. The copy on the main face of the box should read 'Premium Kenyan Tea' The box will contain 25 tagged tea bags, with a net weight of 50 gms.

On one side of the box will read 'packaging instructions' To fully savour this Velan premium tea, use one tea bag for each cup, add some freshly bolded water and wait for 2 minutes as you enjoy the sweet aroma of our tea, stir and serve' Ingredients : Black Tea, and for the others the same : Hibiscus Tea, Green Tea, Purple Tea, White tea. should also feature on the label: Produce of Kenya.

Target Market(s)

Premium

Industry/Entity Type

Agribusiness

Font styles to use
Script

Colors

Designer to choose colors to be used in the design.

Requirements
Must have
• Luxe look and feel
Nice to have
• I have attached the Velan tea logo and images of brands I'd lile the designer to be inspired by.
Should not have
• Green and yellow colours

```html
<!DOCTYPE html>
<html lang="en">
<head>
<meta charset="UTF-8">
<title>Velan Tea – Black Tea Label</title>
<link href="https://fonts.googleapis.com/css2?family=Cinzel:wght@400;600;700&display=swap" rel="stylesheet">
<style>
  :root {
    --page: #ffffff;
    --ink: #231f20;
    --gold: #e8a317;
    --marble-dark: #14110f;
    --marble-mid: #2a211b;
    --marble-tan: #b5835c;
    --label-white: #ffffff;
  }
  * { margin: 0; padding: 0; box-sizing: border-box; }
  html, body {
    width: 1200px;
    height: 800px;
    overflow: hidden;
    background: var(--page);
  }
  body {
    position: relative;
    font-family: "Cinzel", serif;
    color: var(--ink);
  }
  .panel {
    position: absolute;
    top: 167px;
    height: 415px;
  }
  .panel--front { left: 79px; width: 722px; }
  .panel--side { left: 818px; width: 328px; }

  .marble {
    position: absolute;
    inset: 0;
    background:
      radial-gradient(ellipse 18% 10% at 60% 8%, var(--marble-tan), transparent 70%),
      radial-gradient(ellipse 14% 9% at 85% 92%, var(--marble-tan), transparent 70%),
      radial-gradient(ellipse 10% 16% at 4% 60%, var(--marble-tan), transparent 70%),
      radial-gradient(ellipse 10% 14% at 97% 40%, var(--marble-tan), transparent 70%),
      linear-gradient(160deg, var(--marble-dark), var(--marble-mid) 55%, var(--marble-dark));
  }

  .label {
    position: absolute;
    background: var(--label-white);
    border: 1px solid var(--ink);
  }
  .panel--front .label { left: 24px; top: 45px; width: 673px; height: 326px; }
  .panel--side .label { left: 24px; top: 45px; width: 280px; height: 324px; }

  .frame {
    position: absolute;
    inset: 13px 11px;
    border: 5px solid var(--ink);
  }

  .brand-mark {
    position: absolute;
    left: 50%;
    transform: translateX(-50%);
    width: 85px;
    height: 71px;
    background: var(--ink);
    display: flex;
    align-items: flex-end;
    justify-content: center;
    padding-bottom: 16px;
  }
  .brand-mark span {
    font-family: "Cinzel", serif;
    font-weight: 400;
    font-size: 17px;
    color: var(--gold);
    letter-spacing: 0.5px;
  }
  .panel--front .brand-mark { top: 28px; }
  .panel--side .brand-mark { top: 28px; }

  .front-title {
    position: absolute;
    left: 0; right: 0;
    top: 152px;
    text-align: center;
  }
  .front-title .eyebrow {
    font-weight: 600;
    font-size: 18px;
    letter-spacing: 0.5px;
    line-height: 1;
  }
  .front-title .product {
    font-weight: 700;
    font-size: 46px;
    line-height: 1;
    margin-top: 3px;
  }

  .net-weight {
    position: absolute;
    right: 48px;
    top: 253px;
    text-align: center;
    font-weight: 700;
  }
  .net-weight .caption { font-size: 9.5px; letter-spacing: 0.3px; }
  .net-weight .value { font-size: 17px; margin-top: 3px; }

  .side-title {
    position: absolute;
    left: 0; right: 0;
    top: 124px;
    text-align: center;
    font-weight: 700;
    font-size: 24px;
    line-height: 1;
  }
  .instructions {
    position: absolute;
    left: 35px;
    width: 210px;
    top: 165px;
    font-size: 9.2px;
    font-weight: 700;
    line-height: 12.6px;
    text-align: justify;
    text-transform: lowercase;
    font-variant: small-caps;
  }
  .instructions p + p { margin-top: 12px; }
  .instructions .cap { text-transform: none; }
</style>
</head>
<body>

  <section class="panel panel--front">
    <div class="marble" role="img" aria-label="Black and tan marble texture background"></div>
    <div class="label">
      <div class="frame">
        <div class="brand-mark"><span>VELAN</span></div>
        <div class="front-title">
          <div class="eyebrow">PREMIUM KENYAN</div>
          <div class="product">BLACK TEA</div>
        </div>
        <div class="net-weight">
          <div class="caption">NET WEIGHT</div>
          <div class="value">50 GMS</div>
        </div>
      </div>
    </div>
  </section>

  <section class="panel panel--side">
    <div class="marble" role="img" aria-label="Black and tan marble texture background"></div>
    <div class="label">
      <div class="frame">
        <div class="brand-mark"><span>VELAN</span></div>
        <h2 class="side-title">BLACK TEA</h2>
        <div class="instructions">
          <p>To fully savour this Velan premium tea, use one tea bag for each cup, add some freshly bolded water and wait for 2 minutes as you enjoy the sweet aroma of our tea, stir and serve'</p>
          <p>Ingredients : Black Tea</p>
        </div>
      </div>
    </div>
  </section>

</body>
</html>
```